TA BRAMLEY BUSINESS CARD DESIGN PROJECT

We need to utilize our logo that was expertly created on PixelHarbor and now need to match this with a business card design.

```html
<!DOCTYPE html>
<html lang="en">
<head>
<meta charset="utf-8">
<title>TA BRAMLEY Business Cards</title>
<link href="https://fonts.googleapis.com/css2?family=Montserrat:wght@400;500;700;800&display=swap" rel="stylesheet">
<style>
  :root {
    --stage: #2b2b2b;
    --brand-blue: #1158a8;
    --card-black: #161616;
    --ink-white: #ffffff;
    --ink-soft: #e6e6e6;
  }
  * { box-sizing: border-box; margin: 0; padding: 0; }
  html, body {
    width: 1200px; height: 689px; overflow: hidden;
    background: var(--stage);
    font-family: "Montserrat", Arial, sans-serif;
  }
  .stage { position: relative; width: 1200px; height: 689px; }
  .card {
    position: absolute; top: 195px;
    width: 520px; height: 300px; border-radius: 18px; overflow: hidden;
  }
  .card--front { left: 60px; background: var(--brand-blue); }
  .card--back { left: 620px; background: var(--card-black); }

  .wordmark {
    font-weight: 800; letter-spacing: 0.08em; white-space: nowrap;
  }
  .card--front .wordmark {
    position: absolute; left: 0; right: 0; top: 122px;
    text-align: center; font-size: 46px; color: var(--ink-white);
  }
  .card--back .wordmark {
    position: absolute; left: 28px; top: 128px;
    font-size: 26px; color: var(--brand-blue);
  }

  .divider {
    position: absolute; left: 282px; top: 58px;
    width: 1.5px; height: 160px; background: var(--brand-blue);
  }
  .contact {
    position: absolute; left: 300px; top: 52px; color: var(--ink-white);
  }
  .contact__name {
    font-size: 19px; font-weight: 700; color: var(--brand-blue); letter-spacing: 0.02em;
  }
  .contact__role { font-size: 12.5px; font-weight: 500; margin-bottom: 10px; }
  .contact__list { list-style: none; font-size: 12px; line-height: 1.45; }
  .contact__list li { display: flex; align-items: center; gap: 6px; }
  .contact__list svg { width: 10px; height: 10px; fill: var(--brand-blue); flex: none; }
  .contact__address { font-size: 12px; line-height: 1.4; margin-top: 10px; }

  .band { position: absolute; left: 0; top: 0; width: 520px; height: 300px; }
</style>
</head>
<body>
<main class="stage">
  <section class="card card--front" aria-label="Business card front">
    <p class="wordmark">TA BRAMLEY</p>
  </section>

  <section class="card card--back" aria-label="Business card back">
    <p class="wordmark">TA BRAMLEY</p>
    <div class="divider"></div>
    <div class="contact">
      <p class="contact__name">DANIEL REEVE</p>
      <p class="contact__role">Managing Director</p>
      <ul class="contact__list">
        <li><svg viewBox="0 0 10 10"><path d="M2 0.5 L4 2.5 L3 3.8 Q4.5 6 6.2 7 L7.5 6 L9.5 8 L8 9.5 Q3.5 9 0.5 2 Z"/></svg>123 456 789</li>
        <li><svg viewBox="0 0 10 10"><rect x="1" y="3" width="8" height="6" rx="1"/><rect x="3" y="0.5" width="4" height="3"/></svg>123 456 789</li>
        <li><svg viewBox="0 0 10 10"><path d="M0.5 2 H9.5 V8.5 H0.5 Z M0.5 2 L5 5.5 L9.5 2" /></svg>info@tabramleymail.com</li>
        <li><svg viewBox="0 0 10 10"><circle cx="5" cy="5" r="4.5"/></svg>www.tabramley.com</li>
      </ul>
      <p class="contact__address">Your address, City<br>State, Zip 1234</p>
    </div>
    <svg class="band" viewBox="0 0 520 300" aria-hidden="true">
      <polygon points="0,300 0,291 292,291 322,262 520,262 520,300" fill="var(--brand-blue)"/>
      <polyline points="0,282 286,282 314,254" fill="none" stroke="var(--brand-blue)" stroke-width="3"/>
    </svg>
  </section>
</main>
</body>
</html>
```